Verodex business card

Business card for sustainable investment company called "Verodex". Verodex is an exchange platform selling carbon credits between buyers and sellers. Carbon Credits are an environmental commodity for reducing global carbon emissions.

the card should obviously have our logo and the theme should be sustainability/environment mixed with a trading platform.

Contact Information for Business Card

Logo, Name, Title, Phone, Email

Colors
0054AA
0677BA
7BADD7
CADEEF
E8F1F8
0094D4
00A9DD
6FCCEA
C7EBF8
E9F6FB
00AB8E
00BBA5
67D7C9
C6EFE9
E9F9F6
59FF00
82FF00
B8FF75
E3FFCB
F4FFEA

```html
<!DOCTYPE html>
<html lang="en">
<head>
<meta charset="utf-8">
<title>Verodex business card</title>
<link rel="stylesheet" href="https://fonts.googleapis.com/css2?family=Montserrat:wght@500;600;700&family=Roboto+Slab:wght@300;400&display=swap">
<style>
  :root {
    --navy: #13285a;
    --navy-deep: #0f2150;
    --sky: #2ea8e0;
    --sky-light: #42c2ef;
    --white: #ffffff;
    --pattern-a: #f8f8f9;
    --pattern-b: #eceef1;
    --stripe-grey: #d6d9df;
    --backdrop: #e6e8ec;
  }
  * { box-sizing: border-box; margin: 0; padding: 0; }
  html, body {
    width: 1200px; height: 900px; overflow: hidden;
    background: var(--backdrop);
  }
  .canvas { position: relative; width: 1200px; height: 900px; }
  .card {
    position: absolute; left: 250px; width: 700px; height: 400px;
    background: var(--navy); overflow: hidden;
    box-shadow: 0 10px 24px rgba(0,0,0,0.18);
  }
  .card--back { top: 40px; }
  .card--front { top: 460px; }

  .brand {
    position: absolute; display: flex; align-items: center;
    font-family: "Montserrat", sans-serif; font-weight: 600;
    letter-spacing: 0.04em; text-transform: uppercase;
  }
  .brand__mark { display: block; background: var(--sky); }
  .card--back .brand {
    left: 0; right: 0; top: 0; bottom: 0; justify-content: center;
    color: var(--white); font-size: 64px; gap: 26px;
  }
  .card--back .brand__mark { width: 58px; height: 58px; }
  .card--front .brand {
    left: 455px; top: 176px; color: var(--navy); font-size: 34px; gap: 14px;
  }
  .card--front .brand__mark { width: 30px; height: 30px; }

  .front-art { position: absolute; inset: 0; }

  .holder { position: absolute; left: 92px; top: 58px; color: var(--white); }
  .holder__name {
    font-family: "Montserrat", sans-serif; font-weight: 700;
    font-size: 22px; letter-spacing: 0.04em;
  }
  .holder__title {
    font-family: "Montserrat", sans-serif; font-weight: 500;
    font-size: 17px; margin-top: 2px; letter-spacing: 0.02em;
  }
  .contact {
    position: absolute; left: 96px; color: var(--white);
    font-family: "Roboto Slab", serif; font-weight: 300;
    font-size: 15px; line-height: 21px; letter-spacing: 0.02em;
  }
  .contact--phone { top: 142px; }
  .contact--web { top: 206px; }
  .contact--address { top: 270px; }

  .icon-chain { position: absolute; left: 28px; top: 70px; }
</style>
</head>
<body>
<main class="canvas">

  <section class="card card--back" aria-label="Card back">
    <div class="brand"><span class="brand__mark"></span>Verodex</div>
  </section>

  <section class="card card--front" aria-label="Card front">
    <svg class="front-art" width="700" height="400" viewBox="0 0 700 400">
      <defs>
        <linearGradient id="pattern-tone" x1="0" y1="0" x2="1" y2="1">
          <stop offset="0" stop-color="var(--pattern-b)"/>
          <stop offset="0.5" stop-color="var(--pattern-a)"/>
          <stop offset="1" stop-color="var(--pattern-b)"/>
        </linearGradient>
        <linearGradient id="accent-tone" x1="0" y1="0" x2="1" y2="0">
          <stop offset="0" stop-color="var(--sky-light)"/>
          <stop offset="1" stop-color="var(--sky)"/>
        </linearGradient>
      </defs>
      <polygon class="panel-light" role="img" aria-label="Light grey triangle pattern"
               points="468,0 700,0 700,400 565,400 360,195 442,100" fill="url(#pattern-tone)"/>
      <polygon class="accent-top" points="318,0 436,0 418,96" fill="url(#accent-tone)"/>
      <polyline class="stripe-top" points="450,0 430,102" fill="none" stroke="var(--white)" stroke-width="7"/>
      <polyline class="stripe-grey" points="382,112 334,192 408,272" fill="none" stroke="var(--stripe-grey)" stroke-width="7"/>
      <polygon class="accent-bottom" points="410,296 522,400 356,400" fill="url(#accent-tone)"/>
      <polyline class="stripe-bottom" points="420,282 548,400" fill="none" stroke="var(--white)" stroke-width="7"/>
    </svg>

    <div class="brand"><span class="brand__mark"></span>Verodex</div>

    <svg class="icon-chain" width="60" height="260" viewBox="0 0 60 260" aria-hidden="true">
      <line x1="30" y1="20" x2="30" y2="240" stroke="var(--sky)" stroke-width="3"/>
      <g class="icon icon--person" transform="translate(30,22)">
        <polygon points="-24,0 -12,-20 12,-20 24,0 12,20 -12,20" fill="url(#chain-fill)"/>
        <circle cx="0" cy="-4" r="5" fill="var(--white)"/>
        <path d="M-9,10 Q0,-2 9,10 Z" fill="var(--white)"/>
      </g>
      <g class="icon icon--phone" transform="translate(30,86)">
        <polygon points="-22,0 -11,-18 11,-18 22,0 11,18 -11,18" fill="var(--navy)" stroke="var(--sky)" stroke-width="3"/>
        <path d="M-9,-3 Q0,-9 9,-3 L7,1 L3,0 L3,-3 L-3,-3 L-3,0 L-7,1 Z M-6,2 L6,2 L7,8 L-7,8 Z" fill="var(--white)"/>
      </g>
      <g class="icon icon--globe" transform="translate(30,152)">
        <polygon points="-22,0 -11,-18 11,-18 22,0 11,18 -11,18" fill="var(--navy)" stroke="var(--sky)" stroke-width="3"/>
        <g fill="none" stroke="var(--white)" stroke-width="1.4">
          <circle r="8"/><ellipse rx="3.5" ry="8"/><line x1="-8" y1="0" x2="8" y2="0"/>
          <line x1="-7" y1="-4" x2="7" y2="-4"/><line x1="-7" y1="4" x2="7" y2="4"/>
        </g>
      </g>
      <g class="icon icon--pin" transform="translate(30,218)">
        <polygon points="-22,0 -11,-18 11,-18 22,0 11,18 -11,18" fill="var(--navy)" stroke="var(--sky)" stroke-width="3"/>
        <path d="M0,9 C-4,3 -7,0 -7,-3 A7,7 0 1 1 7,-3 C7,0 4,3 0,9 Z" fill="var(--white)"/>
        <circle cx="0" cy="-3" r="2.6" fill="var(--navy)"/>
      </g>
      <defs>
        <linearGradient id="chain-fill" x1="0" y1="0" x2="1" y2="1">
          <stop offset="0" stop-color="var(--sky-light)"/>
          <stop offset="1" stop-color="#2f6fc4"/>
        </linearGradient>
      </defs>
    </svg>

    <div class="holder">
      <p class="holder__name">MARCUS HALE</p>
      <p class="holder__title">Founder</p>
    </div>
    <p class="contact contact--phone">000 5550 4821<br>000 5550 4822</p>
    <p class="contact contact--web">hello@verodex.com<br>www.verodex.com</p>
    <p class="contact contact--address">220, 6th Floor,<br>Elm Street, NY 104420</p>
  </section>

</main>
</body>
</html>
```